Business Card - high end, modern health care

Hey designers!

We need a double sided business card for the boutique, cutting edge physical therapy rehabilitation centre in Sydney's Northern Beaches.

With the most qualified physios in the area The Harbourview Motion Clinic does what other physiotherapy practices do not, we take our time with our patients giving them longer appointments, better physios and therefor faster results!

We guarantee that the service people receive at THMC will be unparalleled.

Hence we need a business card to reflect our modern, boutique, high end service. The final design needs to reflect that we are in a class of our own yet with the feel of beachside retreat.

Below I have attached our logo in both blue on white and white on blue. The exact colour is;
and the font that we have used in our logo is Tex Gyre Aventador.

I like the idea of the blue as the main colour as it is more eye catching and our signage onto the main road will be in this blue and in the interest of consistency across marketing the blue needs to be a part of the design. However I would appreciate a few designs onto a wooden background as this is a visual theme within the fitout of the practice.

The design needs to be of standard size (91x55mm).

Target Market(s)

We target people who have an end outcome in mind and those who have had poor experiences with other providers and ensure that everyone gets the care that they deserve with a premium service that is tailored to the individuals circumstances. As a premium service, the target market is highly educated, business and tech savvy with the additional target market of elderly people who have self funded their retirement and see value in paying for the best ongoing rehabilitation to maintain independence.

Industry/Entity Type

Physical Therapy

Contact Information for Business Card

Name, designation( Titled Musculoskeletal Physiotherapist... there will also be those in the company that have multiple designations ie 5 or 6 words long), phone number, email, facebook, instagram, address

Font styles to use
Sans Serif

Colors

Designer to choose colors to be used in the design.

Requirements
Must have
• Front - The logo as large as possible, blue or wooden theme, and all of the important details.
• Back - A blank space/lines on which to write appointment times (no "Appointment, date, time" etc.)
Nice to have
• facebook url
• logos for facebook and instagram
• Mini logos for the phone and email?

```html
<!DOCTYPE html>
<html lang="en">
<head>
<meta charset="utf-8">
<title>The Harbourview Motion Clinic – Business Card</title>
<link href="https://fonts.googleapis.com/css2?family=Raleway:wght@400;500;700&display=swap" rel="stylesheet">
<style>
  :root {
    --backdrop: #4b4a73;
    --brand-blue: #0e58a8;
    --brand-blue-soft: #2d63ad;
    --card-white: #ffffff;
    --ink: #1b1b1b;
    --rule: #2a2a2a;
    --dash: #9a9a9a;
    --accent-blue: #1b8ad6;
    --accent-pink: #e8639b;
  }
  * { margin: 0; padding: 0; box-sizing: border-box; }
  html, body { width: 1200px; height: 1200px; overflow: hidden; }
  body {
    background: var(--backdrop);
    font-family: "Raleway", sans-serif;
    position: relative;
  }
  .card {
    position: absolute;
    width: 780px;
    height: 445px;
    border-radius: 48px;
    overflow: hidden;
  }
  .card--front { left: 126px; top: 114px; background: var(--brand-blue); }
  .card--back  { left: 291px; top: 632px; background: var(--card-white); }

  .front-emblem {
    position: absolute;
    left: 214px; top: 46px;
    width: 364px; height: 364px;
    border-radius: 50%;
    background: var(--brand-blue-soft);
    opacity: .7;
  }
  .brand {
    position: absolute;
    display: flex;
    align-items: center;
    color: var(--card-white);
    font-weight: 700;
  }
  .brand__dot {
    border-radius: 50%;
    background: currentColor;
    flex: none;
  }
  .brand__name { line-height: 1.05; text-transform: uppercase; white-space: nowrap; }
  .brand__line { display: block; }

  .card--front .brand { left: 154px; top: 178px; gap: 14px; }
  .card--front .brand__dot { width: 82px; height: 82px; }
  .card--front .brand__line--top { font-size: 40px; letter-spacing: 1px; }
  .card--front .brand__line--bottom { font-size: 29px; letter-spacing: 14px; }

  .card--back .brand { left: 54px; top: 72px; gap: 10px; color: var(--brand-blue); }
  .card--back .brand__dot { width: 54px; height: 54px; }
  .card--back .brand__line--top { font-size: 28px; letter-spacing: .5px; }
  .card--back .brand__line--bottom { font-size: 20px; letter-spacing: 10px; }

  .rule {
    position: absolute;
    left: 48px; width: 686px;
    border-top: 1.5px solid var(--rule);
  }
  .rule--top { top: 175px; }
  .rule--mid { top: 297px; border-top-color: #555; }
  .rule--write { top: 402px; border-top: 1.5px dashed var(--dash); }

  .person {
    position: absolute;
    left: 64px; top: 206px;
    width: 232px;
    text-align: right;
    color: var(--ink);
  }
  .person__name { font-size: 30px; font-weight: 400; white-space: nowrap; }
  .person__name em { font-style: normal; color: var(--brand-blue); }
  .person__role { font-size: 17px; font-weight: 500; margin-top: 6px; }

  .contact { position: absolute; left: 389px; top: 208px; color: var(--ink); }
  .contact__item { display: flex; align-items: center; gap: 18px; height: 38px; font-size: 22px; white-space: nowrap; }
  .contact__item svg { width: 28px; height: 28px; flex: none; }

  .social {
    position: absolute;
    left: 61px; top: 320px;
    display: flex; gap: 58px;
    font-size: 18px; font-weight: 500; color: var(--ink);
  }
  .social__item { display: flex; align-items: center; gap: 10px; }
  .social__dot { width: 26px; height: 26px; border-radius: 50%; }
  .social__dot--page { background: var(--accent-blue); }
  .social__dot--handle { background: var(--accent-pink); }
</style>
</head>
<body>

<section class="card card--front" aria-label="Card front">
  <div class="front-emblem"></div>
  <div class="brand">
    <span class="brand__dot"></span>
    <span class="brand__name">
      <span class="brand__line brand__line--top">The Harbourview</span>
      <span class="brand__line brand__line--bottom">Motion Clinic</span>
    </span>
  </div>
</section>

<section class="card card--back" aria-label="Card back">
  <div class="brand">
    <span class="brand__dot"></span>
    <span class="brand__name">
      <span class="brand__line brand__line--top">The Harbourview</span>
      <span class="brand__line brand__line--bottom">Motion Clinic</span>
    </span>
  </div>

  <div class="rule rule--top"></div>

  <div class="person">
    <div class="person__name">Name of <em>Person</em></div>
    <div class="person__role">Designation</div>
  </div>

  <div class="contact">
    <div class="contact__item">
      <svg viewBox="0 0 28 28" aria-hidden="true">
        <circle cx="14" cy="14" r="12.5" fill="none" stroke="#1b1b1b" stroke-width="2"/>
        <path d="M10 8.5c-1.2.6-1.8 1.8-1.3 3.3 1 3 3.5 5.6 6.6 6.8 1.5.5 2.6 0 3.3-1.2l-2.3-1.8-1.3 1c-1.5-.7-2.7-1.9-3.4-3.4l1-1.3z" fill="#1b1b1b"/>
      </svg>
      <span>555.014.2290</span>
    </div>
    <div class="contact__item">
      <svg viewBox="0 0 28 28" aria-hidden="true">
        <rect x="1" y="7" width="26" height="15" fill="#1b1b1b"/>
        <path d="M2 8l12 9 12-9M2 21l9-7M26 21l-9-7" fill="none" stroke="#fff" stroke-width="1.6"/>
      </svg>
      <span>hello@hvmotion.com</span>
    </div>
  </div>

  <div class="rule rule--mid"></div>

  <div class="social">
    <div class="social__item"><span class="social__dot social__dot--page"></span><span>/harbourviewmotion</span></div>
    <div class="social__item"><span class="social__dot social__dot--handle"></span><span>@harbourviewmotion</span></div>
  </div>

  <div class="rule rule--write"></div>
</section>

</body>
</html>
```